Core Value Graphic for a Service Disabled and Minority Certified contractor

My company, Keystone Aid Partners, is a US Federal Contractor that hires veterans and service disabled veterans. Our website is www.keystoneaid7.example. We work hard to maintain a 50:50 split between veterans and non-veterans on our team. Our tagline is "To Find a Better Way." We are continually looking to integrate technology and efficiency into all that we do.

I want a way to express our company core values visually so that our employees and customers alike can read them and get a sense of who we are, what drives us to succeed, and what makes up our team DNA.

I need an artist like you to help me represent our core values visually. In a manner that I can print it out on an 8"X11" sheet of paper or a large 48" X 48" poster, without losing the visual clarity or that it pixelates out of focus. I am looking for a color scheme that is patriotic with Red, White, and Blues and similar hues. I would also like to incorporate my logo and tagline into the design in some manner.

I have attached several examples of a Core Value Grids from other companies. I am hopeful it will inspire you, and a get your brain juices flowing to provide me with a knockout Core Value Grid that will rock only you can provide! I also include a copy of my company Core Values and a copy of our Logo.

Looking forward to seeing your creations. Thanks.

Target Market(s)

Employees, any potential strategic alliance partners, and customers.

Industry/Entity Type

Contractor

Requirements
Must have
• Patriotic feel and have my logo someplace on the document.

```html
<!DOCTYPE html>
<html lang="en">
<head>
<meta charset="utf-8">
<title>Keystone Aid Partners – Core Values</title>
<link rel="stylesheet" href="https://fonts.googleapis.com/css2?family=Montserrat:wght@700&family=Roboto:wght@400;500&family=Roboto+Condensed:wght@400&display=swap">
<style>
  :root{
    --backdrop:#cbcbcb;
    --paper:#ffffff;
    --red:#b00f1a;
    --red-deep:#7c1117;
    --grey:#a9aaac;
    --grey-deep:#6b6c6f;
    --blue:#0b3566;
    --navy:#0d2546;
    --ink:#262626;
    --ink-deep:#111111;
    --gold:#fff200;
    --text-light:#ffffff;
  }
  *{box-sizing:border-box;margin:0;padding:0}
  html,body{width:1200px;height:771px;overflow:hidden;background:var(--backdrop)}
  body{position:relative;font-family:"Roboto",Arial,sans-serif;color:var(--text-light)}

  .sheet{position:absolute;left:189px;top:94px;width:822px;height:582px;background:var(--paper);overflow:hidden}

  .masthead{position:absolute;left:0;top:0;width:822px;height:94px;background:var(--red);border-bottom:3px solid var(--red-deep)}
  .tagline{position:absolute;left:28px;top:33px;font-family:"Montserrat",Arial,sans-serif;font-weight:700;font-size:27px;letter-spacing:1px;color:var(--text-light)}
  .brand{position:absolute;left:604px;top:8px;width:188px;height:78px;background:var(--paper);border-radius:10px;display:flex;align-items:center;justify-content:center;text-align:center}
  .brand-name{font-family:"Roboto",Arial,sans-serif;font-weight:500;font-size:17px;line-height:1.2;color:var(--navy)}

  .panel{position:absolute;font-size:8.2px;line-height:12px;text-align:justify}
  .panel p{margin-bottom:3.4px}

  .strip{position:absolute;display:flex;align-items:center;justify-content:center}
  .strip-text{transform:rotate(-90deg);white-space:nowrap;font-family:"Roboto",Arial,sans-serif;font-weight:500;font-size:16.5px;line-height:18px;text-align:left}

  .safety-strip{left:32px;top:112px;width:56px;height:197px;background:var(--red-deep);border-radius:30px 0 0 30px}
  .safety{left:88px;top:112px;width:319px;height:197px;background:var(--red);padding:14px 12px 0 14px}
  .safety .wrap-curve{float:right;width:130px;height:183px;shape-outside:circle(121px at 146px 132px)}

  .innovation{left:415px;top:112px;width:319px;height:197px;background:var(--grey);padding:14px 14px 0 26px}
  .innovation .wrap-curve{float:left;width:110px;height:183px;shape-outside:circle(121px at -30px 132px)}
  .innovation-strip{left:734px;top:112px;width:56px;height:197px;background:var(--grey-deep);border-radius:0 30px 30px 0}

  .card{position:absolute;top:318px;height:232px}
  .card-head{display:flex;align-items:center;justify-content:center;font-weight:500;font-size:17px}
  .card-body{padding:10px 12px 0 12px;font-size:8.6px;line-height:12.2px;text-align:justify}
  .card-body p{margin-bottom:3.4px}

  .wingman{left:32px;width:247px;background:var(--blue);border-radius:30px 0 0 30px}
  .wingman .card-head{height:41px;background:var(--navy);border-radius:30px 0 0 0}
  .troops{left:289px;width:244px;background:var(--ink)}
  .troops .card-head{height:83px;background:var(--ink-deep);align-items:flex-end;padding-bottom:9px}
  .learn{left:542px;width:248px;background:var(--red);border-radius:0 30px 30px 0}
  .learn .card-head{height:41px;background:var(--red-deep);border-radius:0 30px 0 0}

  .emblem{position:absolute;left:299px;top:146px;width:224px;height:224px}
  .emblem-title{position:absolute;left:299px;top:146px;width:224px;height:224px;display:flex;flex-direction:column;align-items:center;justify-content:center;font-family:"Roboto Condensed","Roboto",sans-serif;color:var(--gold);font-size:54px;line-height:52px;padding-top:4px;-webkit-text-stroke:0.8px var(--gold)}
</style>
</head>
<body>
<main class="sheet">
  <header class="masthead">
    <h1 class="tagline">TO FIND A BETTER WAY</h1>
    <div class="brand"><span class="brand-name">Keystone Aid Partners</span></div>
  </header>

  <div class="strip safety-strip"><span class="strip-text">Everyone comes back<br>to the Green Zone.</span></div>
  <section class="panel safety">
    <div class="wrap-curve"></div>
    <p>WHAT IT MEANS - Safety takes precedence over every phase of the day's operation.</p>
    <p>HOW TO EXPRESS IT - Anyone can call a stop to the work in progress if an unsafe act is occurring. In fact, it is each team member's duty to do so, rectify the unsafe issue, then proceed. Never hesitate; everyone comes back. Finally, each After Action Review begins with discussing safety issues. We always let everyone on the team know of an unsafe situation, so it can be avoided in the future.</p>
    <p>RESULT - All team members go home to their loved ones each day to pursue their individual happiness.</p>
  </section>

  <section class="panel innovation">
    <div class="wrap-curve"></div>
    <p>WHAT IT MEANS: - We weave innovation into the fabric that makes up our company.</p>
    <p>HOW TO EXPRESS IT: - We're early adopters of technology. We quickly evaluate new technologies or processes that could separate us from our competition. Then we implement and evaluate these new technologies. We dump it quickly if we see it is not helping us achieve "Commander's Intent." We have the guts to be first. We iterate continuously and attack, attack, attack.</p>
    <p>RESULT: - We will be ahead of our competition. It' one mechanism that helps us scale. Prosperity favors the bold!</p>
  </section>
  <div class="strip innovation-strip"><span class="strip-text">Boldly go. Seek. Find.</span></div>

  <section class="card wingman">
    <h2 class="card-head">Never leave your wingman</h2>
    <div class="card-body">
      <p>WHAT IT MEANS – We always help your team members be successful. Commitment to each other and to our own personal integrity is the fuel that empowers us.</p>
      <p>HOW TO EXPRESS IT – If a Wingman is having challenges accomplishing their individual priorities or completing their assigned mission, volunteer to help them to do so.</p>
      <p>This goes for Subs/Suppliers as well. We help those who help us succeed! Always look to establish the best win-win relationship possible, and do what you can to support them if they get into a bind.</p>
      <p>RESULT – Be there for them and they will be there for us.</p>
    </div>
  </section>

  <section class="card troops">
    <h2 class="card-head">Troops eat first</h2>
    <div class="card-body">
      <p>WHAT IT MEANS – No leader will put themselves ahead of their subordinates.</p>
      <p>HOW TO EXPRESS IT – We lead by example. Demonstrate the moral courage and discipline to do the right thing at the highest level of quality.</p>
      <p>RESULT – Every new teammember's will quickly realize their leaders genuinely care for their welfare and success.</p>
      <p>This is the best way to drive Esprit de Corps and achieve excellence.</p>
    </div>
  </section>

  <section class="card learn">
    <h2 class="card-head">Fail quickly and learn</h2>
    <div class="card-body">
      <p>WHAT IT MEANS – If you're not making mistakes, you're not taking enough chances or getting out of your comfort zone.</p>
      <p>HOW TO EXPRESS IT – Use your best judgment when trying something new. But, don't let your pride keep you from saying, "I was wrong" when your idea doesn't work. We trust you will know when it's time to dump the idea, or stop doing something that doesn't work.</p>
      <p>RESULT – No one will ever be penalized for making a mistake. Don't be afraid to try something you believe will work. That's how we grow ourselves and our team members.</p>
    </div>
  </section>

  <svg class="emblem" viewBox="0 0 224 224" aria-hidden="true">
    <defs>
      <linearGradient id="emblemGreen" x1="0" y1="0" x2="0" y2="1">
        <stop offset="0" stop-color="#04301a"/>
        <stop offset="0.55" stop-color="#0b6a2c"/>
        <stop offset="1" stop-color="#1ea540"/>
      </linearGradient>
    </defs>
    <circle cx="112" cy="112" r="111" fill="#b7b8ba"/>
    <circle cx="112" cy="112" r="105" fill="#ffffff"/>
    <circle cx="112" cy="112" r="100" fill="url(#emblemGreen)"/>
  </svg>
  <div class="emblem-title"><span>Core</span><span>Values</span></div>
</main>
</body>
</html>
```